Business Card Design Project

We are a construction company in Orange County, CA. We need a two sided business card. We would like the back to be our logo with web URL. Front should included Name, title, address, phone, fax and email address.

our address is
627 West Dorrance Blvd, Suite 308
Anaheim, CA 92718

Our logo files are attached.

Construction

```html
<!DOCTYPE html>
<html lang="en">
<head>
<meta charset="utf-8">
<title>Veltran Business Card</title>
<link href="https://fonts.googleapis.com/css2?family=Arimo:wght@400;700&display=swap" rel="stylesheet">
<style>
  :root {
    --brand-blue: #1b4a80;
    --ink: #2a2a2a;
    --paper: #ffffff;
    --stage: #e9ebee;
  }
  * { margin: 0; padding: 0; box-sizing: border-box; }
  html, body {
    width: 1200px; height: 900px; overflow: hidden;
    background: var(--stage);
    font-family: "Arimo", Arial, sans-serif;
  }
  .card {
    position: absolute;
    left: 285px;
    width: 630px; height: 360px;
    border-radius: 28px;
    overflow: hidden;
    box-shadow: 0 6px 18px rgba(0,0,0,0.18);
  }
  .card-shape { position: absolute; inset: 0; width: 100%; height: 100%; }

  /* Back side */
  .card-back { top: 50px; background: var(--brand-blue); }
  .back-brand {
    position: absolute; left: 0; right: 0; top: 118px;
    text-align: center;
    color: var(--paper);
    font-weight: 700; font-size: 84px; letter-spacing: 2px;
  }
  .back-url {
    position: absolute; right: 80px; bottom: 84px;
    color: var(--paper); font-size: 17px;
  }

  /* Front side */
  .card-front { top: 480px; background: var(--paper); }
  .identity {
    position: absolute; left: 40px; top: 92px; width: 232px;
  }
  .person-name {
    color: var(--brand-blue); font-weight: 700; font-size: 22px;
    text-align: right;
  }
  .person-title {
    color: var(--ink); font-size: 11px; text-align: right; margin-top: 3px;
  }
  .front-brand {
    color: var(--brand-blue); font-weight: 700; font-size: 50px;
    margin-top: 20px; letter-spacing: 1px; text-align: right;
  }
  .divider {
    position: absolute; left: 292px; top: 96px;
    width: 2px; height: 156px; background: var(--brand-blue);
  }
  .contact {
    position: absolute; left: 314px; top: 96px; width: 300px;
  }
  .address {
    color: var(--brand-blue); font-size: 15px; line-height: 19px;
    margin-bottom: 14px;
  }
  .contact-row {
    display: flex; align-items: center;
    height: 22px;
    color: var(--ink); font-size: 16px;
  }
  .contact-icon { width: 14px; height: 14px; margin-right: 28px; flex: none; }
</style>
</head>
<body>

<section class="card card-back" aria-label="Card back">
  <svg class="card-shape" viewBox="0 0 630 360" aria-hidden="true">
    <path d="M0,0 H440 C340,34 140,44 0,84 Z" fill="var(--paper)"/>
    <path d="M190,360 C320,318 510,296 630,280 V360 Z" fill="var(--paper)"/>
  </svg>
  <div class="back-brand">VELTRAN</div>
  <div class="back-url">www.veltranbuild.com</div>
</section>

<section class="card card-front" aria-label="Card front">
  <svg class="card-shape" viewBox="0 0 630 360" aria-hidden="true">
    <path d="M220,0 L600,0 Q570,22 430,24 L300,24 Q240,22 220,0 Z" fill="var(--brand-blue)"/>
    <path d="M150,360 Q168,330 300,328 L470,328 Q560,330 575,360 Z" fill="var(--brand-blue)"/>
  </svg>

  <div class="identity">
    <div class="person-name">Marcus Delany</div>
    <div class="person-title">General Manager</div>
    <div class="front-brand">VELTRAN</div>
  </div>

  <div class="divider"></div>

  <div class="contact">
    <div class="address">627 West Dorrance Blvd, Suite 308<br>Anaheim, CA 92718</div>
    <div class="contact-row">
      <svg class="contact-icon" viewBox="0 0 14 14" aria-hidden="true">
        <path d="M3 1 L5 1 L6 4 L4.5 5.2 Q5.8 8 8.8 9.5 L10 8 L13 9 L13 11 Q13 13 11 13 Q1 12 1 3 Q1 1 3 1 Z" fill="var(--brand-blue)"/>
      </svg>
      <span>(00) 714-5820-316</span>
    </div>
    <div class="contact-row">
      <svg class="contact-icon" viewBox="0 0 14 14" aria-hidden="true">
        <rect x="1" y="4" width="12" height="9" rx="1" fill="var(--brand-blue)"/>
        <rect x="4" y="1" width="6" height="4" fill="var(--brand-blue)"/>
        <rect x="4" y="7" width="6" height="3" fill="var(--paper)"/>
      </svg>
      <span>(00) 714-5820-316</span>
    </div>
    <div class="contact-row">
      <svg class="contact-icon" viewBox="0 0 14 14" aria-hidden="true">
        <rect x="1" y="3" width="12" height="9" rx="1" fill="var(--brand-blue)"/>
        <path d="M1.5 3.5 L7 8 L12.5 3.5" stroke="var(--paper)" stroke-width="1.2" fill="none"/>
      </svg>
      <span>info@veltranbuild.com</span>
    </div>
    <div class="contact-row">
      <svg class="contact-icon" viewBox="0 0 14 14" aria-hidden="true">
        <circle cx="7" cy="7" r="6" fill="var(--brand-blue)"/>
        <path d="M1 7 H13 M7 1 V13 M7 1 Q3 7 7 13 M7 1 Q11 7 7 13" stroke="var(--paper)" stroke-width="0.9" fill="none"/>
      </svg>
      <span>www.veltranbuild.com</span>
    </div>
  </div>
</section>

</body>
</html>
```